QP Fiduciary Website Redesign Contest

We want to refresh our website to be more insitutional, professional for an international audience. We have designed a new logo for this purpose and that has been attached. A full brand brief and positioning statement has also been attached. Please read through all the documents carefully before designing. The old website is found here: https://qp-fiduciary.example/

Target Market(s)

Actuaries and associated businesses internationally

Industry/Entity Type

professional services - actuaries

Number of Pages Required

3 page

Font styles to use
Sans Serif

Colors
0054AA
0677BA
7BADD7
CADEEF
E8F1F8
0094D4
00A9DD
6FCCEA
C7EBF8
E9F6FB
F0912C
F2A743
F7CA91
FBE8D2
FDF5EE
EE7325
F08F49
F5BC92
FAE3D3
FDF4ED
EB3D1F
EC4F4E
F09395
F8D3D4
FCEDEE

Requirements
Must have
• blues and greens to match the logo color, complimentary colors, navigation
Nice to have
• old site: https://qp-fiduciary.example/

```html
<!DOCTYPE html>
<html lang="en">
<head>
<meta charset="utf-8">
<title>QP Fiduciary — Actuarial Software</title>
<link href="https://fonts.googleapis.com/css2?family=Audiowide&family=Inter:wght@400;500;600;700&family=Inter+Tight:wght@600;700&family=Space+Mono&display=swap" rel="stylesheet">
<style>
:root{
  --brand:#0054AA;
  --brand-mid:#0677BA;
  --brand-light:#7BADD7;
  --brand-pale:#CADEEF;
  --brand-soft:#E8F1F8;
  --teal:#0094D4;
  --teal-bright:#00A9DD;
  --teal-light:#6FCCEA;
  --teal-soft:#E9F6FB;
  --cta:#EE7325;
  --cta-soft:#FAE3D3;
  --ink:#10233d;
  --text:#4a5566;
  --muted:#6f7a89;
  --section-bg:#eef4fa;
  --light-bg:#f5f9fc;
  --navy:#0b2545;
  --navy-2:#071a33;
  --white:#fff;
  --line:#dfe7ef;
}
*{box-sizing:border-box;margin:0;padding:0}
html,body{width:1200px;height:4205px;overflow:hidden}
body{font-family:"Inter",sans-serif;color:var(--ink);background:var(--white);position:relative}
section,header,footer{position:absolute;left:0;width:1200px}
.brand{font-family:"Inter",sans-serif;font-weight:600;letter-spacing:2px;display:flex;align-items:center;gap:10px}
.brand-dot{width:14px;height:14px;border-radius:50%;background:var(--teal-bright)}
.btn{display:inline-flex;align-items:center;gap:8px;background:var(--cta);color:var(--white);font-weight:600;border-radius:24px;text-decoration:none;white-space:nowrap}
.section-title{font-family:"Audiowide",sans-serif;font-size:36px;text-align:center;width:100%;letter-spacing:1px;color:var(--ink)}
.section-title span{color:var(--brand)}
.title-rule{width:44px;height:2px;background:var(--teal)}
.section-sub{text-align:center;font-size:14px;line-height:22px;color:var(--text);width:100%}

/* header */
.site-header{top:0;height:80px;background:var(--white);border-bottom:1px solid var(--line)}
.site-header .brand{position:absolute;left:70px;top:26px;font-size:24px;color:var(--brand)}
.nav{position:absolute;left:389px;top:33px;display:flex;gap:36px;font-size:13px}
.nav a{color:var(--ink);text-decoration:none}
.nav a.active{color:var(--teal)}
.site-header .btn{position:absolute;left:882px;top:25px;height:38px;padding:0 20px;font-size:13px}

/* hero */
.hero{top:80px;height:497px;background:linear-gradient(100deg,#0a1f3a 0%,#123462 40%,#1a4a7e 70%,#0f2c52 100%)}
.hero .photo{position:absolute;inset:0;background:linear-gradient(90deg,rgba(5,18,38,.8) 0%,rgba(5,18,38,.4) 55%,rgba(0,148,212,.12) 100%)}
.hero h1{position:absolute;left:78px;top:52px;width:700px;font-family:"Inter Tight",sans-serif;font-weight:700;font-size:62px;line-height:64px;color:var(--white);letter-spacing:-1.5px}
.hero p{position:absolute;left:78px;top:272px;width:540px;color:#dde8f4;font-size:17px;line-height:25px}
.hero .btn{position:absolute;left:78px;top:357px;height:40px;padding:0 26px;font-size:14px}

/* overview */
.overview{top:577px;height:550px;background:var(--white)}
.overview .section-title{position:absolute;top:68px}
.overview .title-rule{position:absolute;left:578px;top:118px}
.overview .section-sub{position:absolute;top:136px;left:300px;width:600px}
.feature-card{position:absolute;top:210px;width:214px;height:253px;background:var(--white);border-radius:6px;box-shadow:0 4px 18px rgba(0,40,90,.09);padding:28px 22px}
.feature-card svg{width:48px;height:48px}
.feature-card h3{font-size:15px;font-weight:600;margin-top:22px;line-height:20px;min-height:40px}
.feature-card .rule{width:30px;height:2px;background:var(--teal);margin:12px 0 18px}
.feature-card p{font-size:12.5px;line-height:19px;color:var(--text)}

/* core solutions */
.solutions{top:1127px;height:683px;background:var(--section-bg)}
.solutions .section-title{position:absolute;top:72px}
.solutions .title-rule{position:absolute;left:578px;top:122px}
.solutions .section-sub{position:absolute;top:140px}
.solutions .photo{position:absolute;left:142px;top:197px;width:423px;height:401px;border-radius:12px;background:linear-gradient(135deg,#e9eef3 0%,#c9d6e3 40%,#1d3452 75%,#0e1d33 100%)}
.solution{position:absolute;left:629px;width:460px}
.solution .icon{position:absolute;left:0;top:0;width:70px;height:70px;border-radius:50%;display:flex;align-items:center;justify-content:center}
.solution .icon.dark{background:var(--brand)}
.solution .icon.light{background:var(--teal)}
.solution .body{position:absolute;left:91px;top:0;width:345px}
.solution h3{font-size:15px;font-weight:600}
.solution p{font-size:12.5px;line-height:19px;color:var(--text);margin-top:8px}
.solution a{display:inline-flex;align-items:center;gap:12px;color:var(--teal);font-size:12.5px;margin-top:10px;text-decoration:none}

/* characteristics */
.characteristics{top:1810px;height:726px;background:var(--white)}
.characteristics .section-title{position:absolute;top:66px}
.characteristics .title-rule{position:absolute;left:578px;top:116px}
.characteristics .section-sub{position:absolute;top:140px}
.hub{position:absolute;left:0;top:0;width:1200px;height:726px}
.hub-brand{position:absolute;left:470px;top:362px;width:275px;justify-content:center;font-size:25px;color:var(--brand)}
.node{position:absolute;width:78px;height:78px;border-radius:50%;display:flex;align-items:center;justify-content:center}
.node.dark{background:var(--brand)}
.node.light{background:var(--teal)}
.trait{position:absolute;width:270px}
.trait h3{font-size:15px;font-weight:600}
.trait p{font-size:12.5px;line-height:19px;color:var(--text);margin-top:6px}
.trait.left{text-align:right}
.characteristics .btn{position:absolute;left:448px;top:597px;height:44px;padding:0 6px 0 24px;font-size:14px;gap:14px}
.btn .round{width:34px;height:34px;border-radius:50%;background:var(--white);display:flex;align-items:center;justify-content:center}

/* insights */
.insights{top:2536px;height:804px;background:var(--light-bg)}
.tag{position:absolute;font-family:"Space Mono",monospace;font-size:10px;letter-spacing:1.5px;padding:3px 12px;border-radius:12px;background:var(--brand-pale);color:var(--brand)}
.insights .tag{left:563px;top:86px}
.insights h2{position:absolute;top:115px;width:100%;text-align:center;font-family:"Inter Tight",sans-serif;font-weight:600;font-size:38px;letter-spacing:-1px}
.insights .section-sub{position:absolute;top:178px;left:340px;width:520px;font-size:13px;color:var(--muted)}
.article{position:absolute;top:276px;width:309px;height:363px;background:var(--white);border-radius:10px;box-shadow:0 3px 14px rgba(0,40,90,.08);overflow:hidden}
.article .thumb{height:193px}
.article .meta{display:flex;gap:14px;font-size:10px;color:var(--muted);padding:18px 20px 0}
.article .meta .cat{color:var(--teal)}
.article h3{font-size:14px;font-weight:600;line-height:20px;padding:10px 20px 0}
.article p{font-size:11px;line-height:17px;color:var(--muted);padding:8px 20px 0}
.article a{display:block;font-size:11px;color:var(--teal);padding:14px 20px 0;text-decoration:none}
.insights .btn{position:absolute;left:517px;top:677px;height:40px;padding:0 26px;font-size:13px}

/* cta */
.cta{top:3340px;height:490px;background:linear-gradient(90deg,#071a33 0%,#0c2a50 45%,#14406e 72%,#0c2a50 100%)}
.cta .photo{position:absolute;inset:0;background:linear-gradient(90deg,rgba(4,14,30,.85) 0%,rgba(4,14,30,.5) 45%,rgba(0,148,212,.08) 100%)}
.cta .tag{left:107px;top:109px;background:#123c6b;color:var(--teal-light)}
.cta h2{position:absolute;left:107px;top:145px;font-family:"Inter Tight",sans-serif;font-weight:700;font-size:38px;line-height:40px;color:var(--white);letter-spacing:-1px}
.cta p{position:absolute;left:107px;top:242px;width:420px;color:#d2def0;font-size:14px;line-height:23px}
.cta .btn{position:absolute;left:107px;top:343px;height:38px;padding:0 26px;font-size:13px}

/* footer */
.site-footer{top:3830px;height:375px;background:var(--navy)}
.site-footer .brand{position:absolute;left:142px;top:62px;font-size:32px;color:var(--white)}
.site-footer .about{position:absolute;left:142px;top:138px;width:320px;font-size:12.5px;line-height:19px;color:#c6d4e6}
.col-title{position:absolute;top:66px;font-family:"Audiowide",sans-serif;font-size:16px;font-weight:400;color:var(--white)}
.links{position:absolute;left:576px;top:110px;list-style:none;font-size:12.5px;line-height:25.5px}
.links a{color:#d6e2f0;text-decoration:none}
.contact{position:absolute;left:813px;width:280px;display:flex;gap:12px;font-size:12.5px;color:#d6e2f0;line-height:19px}
.contact strong{font-family:"Audiowide",sans-serif;font-weight:400;color:var(--white);font-size:14px}
.footer-rule{position:absolute;left:142px;top:299px;width:935px;height:1px;background:#21456f}
.legal{position:absolute;left:142px;top:325px;font-size:12px;color:#c6d4e6}
.legal span{margin-left:22px}
.socials{position:absolute;left:948px;top:318px;display:flex;gap:8px}
.socials a{width:30px;height:30px;border-radius:50%;display:block}
.socials a:nth-child(1){background:var(--teal-bright)}
.socials a:nth-child(2),.socials a:nth-child(3){border:1.5px solid var(--white)}
</style>
</head>
<body>

<header class="site-header">
  <div class="brand"><i class="brand-dot"></i>QP FIDUCIARY</div>
  <nav class="nav">
    <a class="active" href="#">Home</a><a href="#">Platform</a><a href="#">Solutions</a><a href="#">Insights</a><a href="#">Company</a><a href="#">Contact</a>
  </nav>
  <a class="btn" href="#">Request a Technical Walkthrough</a>
</header>

<section class="hero">
  <div class="photo" role="img" aria-label="Analyst working at a desk in front of monitors showing financial charts"></div>
  <h1>Actuarial Software For Structured, Auditable Financial Analysis.</h1>
  <p>QP Fiduciary develops software that transforms established actuarial methodologies into compliant, decision-ready tools.</p>
  <a class="btn" href="#">Request a Technical Walkthrough <svg width="12" height="12" viewBox="0 0 12 12"><path d="M1 6h9M6 2l4 4-4 4" stroke="#fff" stroke-width="1.6" fill="none"/></svg></a>
</section>

<section class="overview">
  <h2 class="section-title">PLATFORM <span>OVERVIEW</span></h2>
  <div class="title-rule"></div>
  <p class="section-sub">Our platform empowers actuaries and risk professionals with tools designed for modern regulatory and business demands.</p>

  <article class="feature-card" style="left:142px">
    <svg viewBox="0 0 48 48"><circle cx="30" cy="18" r="14" fill="#E9F6FB"/><rect x="4" y="8" width="38" height="26" rx="2" fill="none" stroke="#0054AA" stroke-width="1.6"/><path d="M16 40h14M23 34v6" stroke="#0054AA" stroke-width="1.6"/><circle cx="23" cy="15" r="3" fill="none" stroke="#0094D4" stroke-width="1.5"/><path d="M23 18v4M13 22h20M13 22v4M23 22v4M33 22v4" stroke="#0094D4" stroke-width="1.5" fill="none"/></svg>
    <h3>Structured Workflows</h3><div class="rule"></div>
    <p>that guide users through every step of the analysis process</p>
  </article>
  <article class="feature-card" style="left:376px">
    <svg viewBox="0 0 48 48"><circle cx="26" cy="20" r="15" fill="#0094D4"/><circle cx="20" cy="26" r="15" fill="none" stroke="#0054AA" stroke-width="1.6"/><path d="M14 13l18 18M20 11l14 14M12 18l14 14" stroke="#fff" stroke-width="1.5"/></svg>
    <h3>Full Transparency Of Assumptions</h3><div class="rule"></div>
    <p>that guide users through every step of the analysis process</p>
  </article>
  <article class="feature-card" style="left:609px">
    <svg viewBox="0 0 48 48"><circle cx="32" cy="30" r="12" fill="#E9F6FB"/><rect x="6" y="4" width="26" height="34" rx="2" fill="none" stroke="#0054AA" stroke-width="1.6"/><path d="M11 12h16M11 18h16M11 24h10" stroke="#0054AA" stroke-width="1.5"/><circle cx="30" cy="30" r="7" fill="#fff" stroke="#0094D4" stroke-width="1.6"/><path d="M35 35l7 7" stroke="#0094D4" stroke-width="2"/></svg>
    <h3>Built-in Auditability</h3><div class="rule"></div>
    <p>that guide users through every step of the analysis process</p>
  </article>
  <article class="feature-card" style="left:843px">
    <svg viewBox="0 0 48 48"><circle cx="24" cy="24" r="20" fill="none" stroke="#00A9DD" stroke-width="2" stroke-dasharray="4 3"/><circle cx="24" cy="24" r="14" fill="#0054AA"/><path d="M15 21l9-5 9 5zM17 23v8M22 23v8M27 23v8M32 23v8M15 32h18" stroke="#fff" stroke-width="1.5" fill="none"/></svg>
    <h3>Robust Governance Features</h3><div class="rule"></div>
    <p>that guide users through every step of the analysis process</p>
  </article>
</section>

<section class="solutions">
  <h2 class="section-title">CORE <span>SOLUTIONS</span></h2>
  <div class="title-rule"></div>
  <p class="section-sub">Precision-built modules for the most demanding actuarial tasks</p>
  <div class="photo" role="img" aria-label="Two hands joining puzzle pieces"></div>

  <div class="solution" style="top:204px">
    <div class="icon dark"><svg width="34" height="34" viewBox="0 0 34 34"><circle cx="20" cy="12" r="7" fill="none" stroke="#fff" stroke-width="1.5"/><path d="M20 5v7h7" stroke="#fff" stroke-width="1.5" fill="none"/><path d="M4 26l6-4h8l6 2 6-4M4 30h22" stroke="#fff" stroke-width="1.5" fill="none"/></svg></div>
    <div class="body"><h3>Reserving &amp; Valuation</h3><p>Perform compliant, repeatable reserving and valuation processes with full traceability and support for multiple actuarial methods and regulatory frameworks.</p><a href="#">Learn More <svg width="16" height="10" viewBox="0 0 16 10"><path d="M0 5h14M10 1l4 4-4 4" stroke="#0094D4" stroke-width="1.5" fill="none"/></svg></a></div>
  </div>
  <div class="solution" style="top:353px">
    <div class="icon light"><svg width="34" height="34" viewBox="0 0 34 34"><path d="M8 4h13l5 5v21H8z" fill="none" stroke="#fff" stroke-width="1.5"/><circle cx="21" cy="22" r="6" fill="none" stroke="#fff" stroke-width="1.5"/><path d="M12 11h8M12 15h6" stroke="#fff" stroke-width="1.5"/></svg></div>
    <div class="body"><h3>Pricing</h3><p>Build and test pricing models with transparent assumptions, scenario testing, and comparative analytics to support profitable product development.</p><a href="#">Learn More <svg width="16" height="10" viewBox="0 0 16 10"><path d="M0 5h14M10 1l4 4-4 4" stroke="#0094D4" stroke-width="1.5" fill="none"/></svg></a></div>
  </div>
  <div class="solution" style="top:501px">
    <div class="icon dark"><svg width="34" height="34" viewBox="0 0 34 34"><circle cx="17" cy="13" r="8" fill="none" stroke="#fff" stroke-width="1.5" stroke-dasharray="3 2"/><path d="M17 8v5l3 3" stroke="#fff" stroke-width="1.5" fill="none"/><path d="M4 27l6-4h8l6 2 6-4" stroke="#fff" stroke-width="1.5" fill="none"/></svg></div>
    <div class="body"><h3>Enterprise Risk Management</h3><p>Integrate risk metrics, stress testing, and capital modeling in a governed environment to support ORSA, Solvency II, and other ERM requirements.</p><a href="#">Learn More <svg width="16" height="10" viewBox="0 0 16 10"><path d="M0 5h14M10 1l4 4-4 4" stroke="#0094D4" stroke-width="1.5" fill="none"/></svg></a></div>
  </div>
</section>

<section class="characteristics">
  <h2 class="section-title">PLATFORM <span>CHARACTERISTICS</span></h2>
  <div class="title-rule"></div>
  <p class="section-sub">Engineered for clarity, built to scale across borders</p>

  <svg class="hub" viewBox="0 0 1200 726"><circle cx="600" cy="378" r="174" fill="none" stroke="#7BADD7" stroke-width="2"/></svg>
  <div class="brand hub-brand"><i class="brand-dot"></i>QP FIDUCIARY</div>

  <div class="node dark" style="left:444px;top:225px"><svg width="36" height="36" viewBox="0 0 36 36"><circle cx="18" cy="8" r="4" fill="none" stroke="#fff" stroke-width="1.5"/><path d="M18 12v6M8 18h20M8 18v5M18 18v5M28 18v5" stroke="#fff" stroke-width="1.5"/><rect x="5" y="23" width="6" height="6" fill="none" stroke="#fff" stroke-width="1.5"/><rect x="15" y="23" width="6" height="6" fill="none" stroke="#fff" stroke-width="1.5"/><rect x="25" y="23" width="6" height="6" fill="none" stroke="#fff" stroke-width="1.5"/></svg></div>
  <div class="node light" style="left:678px;top:225px"><svg width="36" height="36" viewBox="0 0 36 36"><circle cx="13" cy="12" r="5" fill="none" stroke="#fff" stroke-width="1.5"/><path d="M4 30c0-6 4-10 9-10s9 4 9 10" fill="none" stroke="#fff" stroke-width="1.5"/><circle cx="26" cy="20" r="6" fill="none" stroke="#fff" stroke-width="1.5"/><path d="M23 20l2 2 4-4" stroke="#fff" stroke-width="1.5" fill="none"/></svg></div>
  <div class="node light" style="left:444px;top:457px"><svg width="36" height="36" viewBox="0 0 36 36"><path d="M8 4h14l6 6v22H8z" fill="none" stroke="#fff" stroke-width="1.5"/><circle cx="18" cy="19" r="6" fill="none" stroke="#fff" stroke-width="1.5"/><path d="M22 23l5 5" stroke="#fff" stroke-width="1.8"/></svg></div>
  <div class="node dark" style="left:678px;top:457px"><svg width="36" height="36" viewBox="0 0 36 36"><circle cx="16" cy="16" r="10" fill="none" stroke="#fff" stroke-width="1.5"/><path d="M11 20v-4M16 20v-8M21 20v-6" stroke="#fff" stroke-width="1.5"/><path d="M23 23l8 8" stroke="#fff" stroke-width="2"/></svg></div>

  <div class="trait left" style="left:148px;top:232px"><h3>Structured Workflows</h3><p>Consistent, repeatable processes from data to disclosure.</p></div>
  <div class="trait" style="left:781px;top:232px"><h3>Multi-jurisdictional Review Support</h3><p>Localise assumptions, outputs, and reports for any regulator.</p></div>
  <div class="trait left" style="left:148px;top:465px"><h3>Transparent Assumptions</h3><p>Every assumption exposed, documented, and linked to source.</p></div>
  <div class="trait" style="left:781px;top:465px"><h3>Comparative Analysis Capability</h3><p>Run scenarios side by side — instantly see impacts.</p></div>

  <a class="btn" href="#">Request A Technical Walkthrough <span class="round"><svg width="14" height="12" viewBox="0 0 14 12"><path d="M1 6h11M8 2l4 4-4 4" stroke="#EE7325" stroke-width="1.6" fill="none"/></svg></span></a>
</section>

<section class="insights">
  <span class="tag">INSIGHTS</span>
  <h2>Insights &amp; Thought Leadership</h2>
  <p class="section-sub">Key publications that set our platform apart in delivering reliable, governance-ready actuarial analysis.</p>

  <article class="article" style="left:114px">
    <div class="thumb" role="img" aria-label="Printed financial reports with charts on a desk" style="background:linear-gradient(135deg,#5b4636 0%,#c9ccd2 55%,#e8edf2 100%)"></div>
    <div class="meta"><span>24 Jul 2025</span><span class="cat">Governance</span></div>
    <h3>RBC (Risk-Based Capital)</h3>
    <p>Harbor Point, 24 July 2025 — QP Fiduciary, an independent actuarial consulting firm...</p>
    <a href="#">Read More →</a>
  </article>
  <article class="article" style="left:447px">
    <div class="thumb" role="img" aria-label="Dark analytics dashboard with colourful bar charts" style="background:linear-gradient(135deg,#0b1628 0%,#15284a 60%,#1f3c6a 100%)"></div>
    <div class="meta"><span>15 Jan 2026</span><span class="cat">Technology</span></div>
    <h3>Evolution Into Technology-Led Actuarial Platforms</h3>
    <p>Harbor Point, January 12, 2026 — QP Fiduciary is rethinking the actuarial workflow...</p>
    <a href="#">Read More →</a>
  </article>
  <article class="article" style="left:782px">
    <div class="thumb" role="img" aria-label="Printed reporting standard document on a wooden table" style="background:linear-gradient(135deg,#5a3a26 0%,#f1efeb 45%,#e4e1dc 70%,#7a5338 100%)"></div>
    <div class="meta"><span>17 Jan 2025</span><span class="cat">Governance</span></div>
    <h3>IFRS 17: A Paradigm Shift For Financial Reporting</h3>
    <p>Harbor Point, January 17, 2026 — QP Fiduciary is an actuarial consulting firm leading...</p>
    <a href="#">Read More →</a>
  </article>

  <a class="btn" href="#">View All Articles →</a>
</section>

<section class="cta">
  <div class="photo" role="img" aria-label="Professional working on a laptop in a dim office"></div>
  <span class="tag">SCHEDULE A DEMO</span>
  <h2>Ready To Transform<br>Your Actuarial Practice?</h2>
  <p>Discover how QP Fiduciary's platform can bring structure, transparency, and confidence to your financial analysis workflows.</p>
  <a class="btn" href="#">Request a Technical Walkthrough →</a>
</section>

<footer class="site-footer">
  <div class="brand"><i class="brand-dot"></i>QP FIDUCIARY</div>
  <p class="about">Software that translates actuarial methodologies into disciplined decision-ready analytical tools across diverse regulatory environments.</p>

  <h4 class="col-title" style="left:576px">QUICK LINKS</h4>
  <ul class="links">
    <li><a href="#">Home</a></li><li><a href="#">Platform</a></li><li><a href="#">Solutions</a></li><li><a href="#">Insights</a></li><li><a href="#">Company</a></li><li><a href="#">Contact</a></li>
  </ul>

  <h4 class="col-title" style="left:813px">CONTACT DETAILS</h4>
  <div class="contact" style="top:112px"><svg width="14" height="18" viewBox="0 0 14 18"><path d="M7 0a7 7 0 0 0-7 7c0 5 7 11 7 11s7-6 7-11a7 7 0 0 0-7-7z" fill="#6FCCEA"/><circle cx="7" cy="7" r="2.5" fill="#0b2545"/></svg><div><strong>QP FIDUCIARY, Inc.</strong><br>410 Meridian Court, Suite 12<br>Harbor Point, FL 30000</div></div>
  <div class="contact" style="top:196px;align-items:center"><svg width="15" height="15" viewBox="0 0 24 24"><path d="M6.6 10.8a15 15 0 0 0 6.6 6.6l2.2-2.2a1 1 0 0 1 1-.25 11.4 11.4 0 0 0 3.6.57 1 1 0 0 1 1 1V20a1 1 0 0 1-1 1A17 17 0 0 1 3 4a1 1 0 0 1 1-1h3.5a1 1 0 0 1 1 1c0 1.25.2 2.45.57 3.57a1 1 0 0 1-.25 1z" fill="#6FCCEA"/></svg><span style="font-size:14px;color:#fff">+1(555)010-2840</span></div>
  <div class="contact" style="top:236px;align-items:center"><svg width="15" height="12" viewBox="0 0 15 12"><rect width="15" height="12" rx="1" fill="#6FCCEA"/><path d="M1 1l6.5 5L14 1" stroke="#0b2545" stroke-width="1.3" fill="none"/></svg><span>hello@qp-fiduciary.example</span></div>

  <div class="footer-rule"></div>
  <p class="legal">© 2026 QP Fiduciary. All rights reserved.<span>Privacy · Terms</span></p>
  <div class="socials"><a href="#" aria-label="Social profile"></a><a href="#" aria-label="Social profile"></a><a href="#" aria-label="Social profile"></a></div>
</footer>

</body>
</html>
```